QVR business card

Need a business card for a company that provides instructional design and elearning development services. The website is here: http://quorvane.studio/

I'm attaching a current logo, as well as the old business card design. While I like to keep it clean, the old design is too simplistic for my liking. The only idea I want to reuse from the old design is placing industry jargon on the back of the card, just need a better way to present it. But if you have other ideas for the back--feel free to experiment.

Please use the colors complementary to the color we have on the website. Thank you!

```html
<!DOCTYPE html>
<html lang="en">
<head>
<meta charset="utf-8">
<title>QVR Business Card</title>
<link href="https://fonts.googleapis.com/css2?family=Montserrat:wght@600;700&family=Roboto+Condensed:wght@700&family=Roboto:wght@400;500&display=swap" rel="stylesheet">
<style>
  :root {
    --backdrop: #e4e4e4;
    --card-dark: #323334;
    --card-light: #fbfbfb;
    --teal: #1fae99;
    --gold: #d6cc8a;
    --ink: #2b2b2b;
    --white: #ffffff;
  }
  html, body {
    margin: 0;
    width: 1200px;
    height: 1200px;
    overflow: hidden;
    background: var(--backdrop);
  }
  .canvas { position: relative; width: 1200px; height: 1200px; }

  .card-front {
    position: absolute;
    left: 238px; top: 118px;
    width: 714px; height: 419px;
  }
  .jargon { font-family: "Montserrat", sans-serif; font-weight: 700; fill: var(--teal); }
  .headline { font-family: "Roboto Condensed", sans-serif; font-weight: 700; fill: var(--white); }

  .card-back {
    position: absolute;
    left: 232px; top: 645px;
    width: 710px; height: 415px;
    background: var(--card-light);
    border-radius: 22px;
    overflow: hidden;
  }
  .brand {
    position: absolute;
    left: 60px; top: 50px;
    display: flex; align-items: center; gap: 14px;
  }
  .brand-mark { width: 44px; height: 44px; background: var(--teal); }
  .brand-name {
    font-family: "Montserrat", sans-serif;
    font-weight: 700;
    font-size: 52px;
    letter-spacing: 2px;
    color: var(--gold);
    line-height: 1;
  }
  .contact {
    position: absolute;
    left: 334px; top: 220px;
    font-family: "Roboto", sans-serif;
    color: var(--ink);
  }
  .contact-name {
    font-family: "Montserrat", sans-serif;
    font-weight: 600;
    font-size: 22px;
    margin: 0 0 24px;
  }
  .contact-list { list-style: none; margin: 0; padding: 0; }
  .contact-list li {
    display: flex; align-items: center; gap: 18px;
    font-size: 17px;
    height: 27px;
  }
  .contact-list svg { width: 16px; height: 16px; fill: var(--teal); }
  .accent-band { position: absolute; left: 0; bottom: 0; width: 710px; height: 19px; }
</style>
</head>
<body>
<main class="canvas">

  <svg class="card-front" viewBox="0 0 714 419" aria-label="Card front: industry jargon">
    <rect width="714" height="419" rx="22" fill="var(--card-dark)"/>
    <text class="jargon" x="42" y="59" font-size="40" textLength="630" lengthAdjust="spacingAndGlyphs">MOBILE LEARNING SCORM</text>
    <text class="jargon" x="42" y="113" font-size="40" textLength="630" lengthAdjust="spacingAndGlyphs">INSTRUCTIONAL DESIGN LMS</text>
    <text class="jargon" x="42" y="166" font-size="40" textLength="630" lengthAdjust="spacingAndGlyphs">MOOCS ELEARNING HTML5</text>
    <rect x="0" y="204" width="30" height="36" fill="var(--white)"/>
    <rect x="688" y="204" width="26" height="36" fill="var(--white)"/>
    <text class="headline" x="42" y="240" font-size="72" textLength="630" lengthAdjust="spacingAndGlyphs">HOW CAN WE HELP?</text>
    <text class="jargon" x="42" y="285" font-size="40" textLength="632" lengthAdjust="spacingAndGlyphs">ADULT LEARNING THEORY</text>
    <text class="jargon" x="42" y="339" font-size="40" textLength="632" lengthAdjust="spacingAndGlyphs">GAMIFICATION CLASSROOM</text>
    <text class="jargon" x="42" y="392" font-size="40" textLength="634" lengthAdjust="spacingAndGlyphs">XAPI BLENDED LEARNING</text>
  </svg>

  <section class="card-back" aria-label="Card back: contact details">
    <div class="brand">
      <span class="brand-mark"></span>
      <span class="brand-name">QVR</span>
    </div>

    <div class="contact">
      <p class="contact-name">Dorian Velk</p>
      <ul class="contact-list">
        <li>
          <svg viewBox="0 0 16 16" aria-hidden="true"><path d="M2 5c0-2 3-3 6-3s6 1 6 3v1h-3V5H5v1H2zM4 7h8l2 6H2z"/></svg>
          555-013-2847
        </li>
        <li>
          <svg viewBox="0 0 16 16" aria-hidden="true"><path d="M8 1a7 7 0 1 0 0 14A7 7 0 0 0 8 1zm0 1.5c.8 0 1.7 1.5 2 4H6c.3-2.5 1.2-4 2-4zM2.6 7h2.4v2H2.6A5.5 5.5 0 0 1 2.6 7zm3.4 2V7h4v2zm5 0V7h2.4a5.5 5.5 0 0 1 0 2zM6 10h4c-.3 2.5-1.2 4-2 4s-1.7-1.5-2-4z"/></svg>
          www.quorvane.studio
        </li>
        <li>
          <svg viewBox="0 0 16 16" aria-hidden="true"><path d="M1 3h14v10H1zm1.5 1.5L8 9l5.5-4.5v-.2h-11z"/></svg>
          dvelk@quorvane.studio
        </li>
      </ul>
    </div>

    <svg class="accent-band" viewBox="0 0 710 19" preserveAspectRatio="none" aria-hidden="true">
      <rect width="710" height="19" fill="var(--gold)"/>
      <polygon points="0,0 500,0 450,19 0,19" fill="var(--teal)"/>
    </svg>
  </section>

</main>
</body>
</html>
```